Need Help having my business card stand out

I am the owner of Birchway Canine Training and would like for my business cards to stand out. I have been trying to keep designing them myself but I can't get what I have in my head on the card. I will try my best to post templates that I like for inspirations. I want something unique but elegant. I don't want in to look cartoony or cheesy. It needs to pop in a pet shop but also in a coffee shop or gym.

Target Market(s)

Dog owners, Married ,No young kids Jr High school kids and up (maybe kids on the way) Executives, Stay at home moms/wives, Small business owners

Industry/Entity Type

Dog Training

Contact Information for Business Card

Lowell Spratt, 281-904-3376, info@birchwaycanine.example, www.birchwaycanine.example

Colors

Designer to choose colors to be used in the design.

Requirements
Must have
• my logo
Should not have
• Cursive lettering

```html
<!DOCTYPE html>
<html lang="en">
<head>
<meta charset="utf-8">
<title>Birchway Canine Training – Round Business Card</title>
<link rel="stylesheet" href="https://fonts.googleapis.com/css2?family=Open+Sans:wght@400;600;700&display=swap">
<style>
  :root {
    --backdrop: #3f3f3f;
    --card-light: #ffffff;
    --card-dark: #000000;
    --ink-dark: #111111;
    --ink-light: #ffffff;
    --shadow: rgba(0, 0, 0, 0.35);
  }
  * { margin: 0; padding: 0; box-sizing: border-box; }
  html, body {
    width: 1200px;
    height: 900px;
    overflow: hidden;
    background: var(--backdrop);
    font-family: "Open Sans", Arial, sans-serif;
  }
  .canvas {
    position: relative;
    width: 1200px;
    height: 900px;
  }
  .card {
    position: absolute;
    top: 215px;
    width: 414px;
    height: 414px;
    border-radius: 50%;
    box-shadow: 0 2px 6px var(--shadow);
    display: flex;
    flex-direction: column;
    align-items: center;
  }
  .card-front {
    left: 164px;
    background: var(--card-light);
    justify-content: center;
  }
  .card-back {
    left: 623px;
    background: var(--card-dark);
    color: var(--ink-light);
  }
  .brand {
    display: flex;
    flex-direction: column;
    align-items: center;
    gap: 18px;
    margin-top: 8px;
  }
  .brand-mark {
    width: 96px;
    height: 96px;
    border-radius: 50%;
    background: var(--ink-dark);
  }
  .brand-name {
    color: var(--ink-dark);
    font-weight: 700;
    font-size: 34px;
    line-height: 1.12;
    text-align: center;
    text-transform: uppercase;
    letter-spacing: 0.5px;
  }
  .holder-name {
    margin-top: 112px;
    font-weight: 600;
    font-size: 24px;
    letter-spacing: 0.3px;
    text-transform: uppercase;
  }
  .contact-icons {
    margin-top: 50px;
    display: flex;
    gap: 6px;
  }
  .contact-icons svg { width: 18px; height: 18px; fill: var(--ink-light); }
  .contact-list {
    margin-top: 12px;
    list-style: none;
    text-align: center;
    font-size: 18px;
    line-height: 24px;
  }
</style>
</head>
<body>
<main class="canvas">
  <section class="card card-front">
    <div class="brand">
      <span class="brand-mark"></span>
      <p class="brand-name">Birchway<br>Canine<br>Training</p>
    </div>
  </section>

  <section class="card card-back">
    <h1 class="holder-name">Lowell Spratt</h1>
    <div class="contact-icons" aria-hidden="true">
      <svg viewBox="0 0 24 24"><path d="M6.6 10.8a15.1 15.1 0 0 0 6.6 6.6l2.2-2.2c.3-.3.7-.4 1-.2 1.1.4 2.3.6 3.6.6.6 0 1 .4 1 1V20c0 .6-.4 1-1 1A17 17 0 0 1 3 4c0-.6.4-1 1-1h3.5c.6 0 1 .4 1 1 0 1.3.2 2.5.6 3.6.1.3 0 .7-.2 1z"/></svg>
      <svg viewBox="0 0 24 24"><path d="M2 5h20v1.4l-10 7.4L2 6.4z"/><path d="M2 8.6l10 7.4 10-7.4V19H2z"/></svg>
      <svg viewBox="0 0 24 24"><circle cx="12" cy="12" r="10"/><path d="M7 7c2 1 3 3 2 5s1 3 2 5M15 5c-1 2 0 3 2 4s2 3 2 5" fill="none" stroke="#000" stroke-width="1.6"/></svg>
    </div>
    <ul class="contact-list">
      <li>281-904-3376</li>
      <li>info@birchwaycanine.example</li>
      <li>www.birchwaycanine.example</li>
    </ul>
  </section>
</main>
</body>
</html>
```